Business Card Design for Retail Product Line

We need a two-sided, full-color business card for a new oral care product line. The feel of the card should invoke emotions of happiness and health. It should be bright, cheerful and modern in appearance. The card should be mostly matte finish, but with elements of spot-gloss and/or raised/embossed features (print, logo, tag lines, etc.).

Target Market(s)

People who are into whole-body health, eat well and understand the importance of nutrition.

Industry/Entity Type

Health And Wellness

Contact Information for Business Card

The logo, color scheme and tag-lines have all been developed and artwork is attached. Card is to be standard-sized and should use a mix of clean, sans-serif fonts; the main font (DIN) is attached as well. The card will be used for 3 individuals and should include placeholders for:
1. Name
2. Title (for example, "CEO")
3. Business address
4. Phone number
5. Website
6. Email address

Font styles to use
Sans Serif
Other font styles liked:
• DIN font

Colors
faa54b
000000
5c5c5c
a2ce44

Requirements
Must have
• 2 sides
• Full color orange on one side
• Image of DNA leaves
• Tag line "Glow From The Roots Up", on single side with orange background
• Company Logo (Plure) on same side as text (name, phone, address, etc.)
• Name, Title, Business Address, Phone Number, Website, Email address
• UPDATE: "Brisk Meadow", not "Brisk M Eadow"
Should not have
• Calligraphy
• Dark colors
• UPDATE!! Do not include "Turmeric infused toothpaste" on the business card
• UPDATE #2!! Do not include "Brisk Meadow" on the business card

```html
<!DOCTYPE html>
<html lang="en">
<head>
<meta charset="utf-8">
<title>Plure business card, front and back</title>
<link rel="stylesheet" href="https://fonts.googleapis.com/css2?family=Barlow:wght@400;500;600;700;800&display=swap">
<style>
  :root {
    --page: #ece6dc;
    --sun-light: #f3cf3f;
    --sun-deep: #e8962f;
    --slate: #4b4b4b;
    --leaf: #8dc63f;
    --leaf-deep: #1f9a4a;
    --helix: #d6d6d6;
    --white: #ffffff;
    --dots: #e8e8e8;
  }
  * { box-sizing: border-box; margin: 0; padding: 0; }
  html, body {
    width: 1200px; height: 1076px; overflow: hidden;
    background: var(--page);
    font-family: "Barlow", "Helvetica Neue", Arial, sans-serif;
  }
  .sheet { position: relative; width: 1200px; height: 1076px; }
  .card {
    position: absolute; left: 220px;
    width: 760px; height: 434px;
    border-radius: 34px;
    overflow: hidden;
    box-shadow: 0 10px 24px rgba(0,0,0,0.18);
  }
  /* Tagline side */
  .card--tagline {
    top: 64px;
    background: linear-gradient(160deg, var(--sun-deep) 0%, var(--sun-light) 40%, var(--sun-light) 62%, var(--sun-deep) 100%);
    color: var(--white);
  }
  .tagline {
    position: absolute; left: 250px; top: 108px;
    line-height: 0.9;
    text-transform: uppercase;
  }
  .tagline__lead {
    display: block;
    font-size: 108px; font-weight: 700;
    text-transform: lowercase;
    letter-spacing: -1px;
    margin-bottom: 12px;
  }
  .tagline__rest {
    display: block;
    font-size: 52px; font-weight: 600;
    letter-spacing: 0.5px;
  }
  .website {
    position: absolute; left: 0; right: 0; bottom: 30px;
    text-align: center;
    font-size: 17px; font-weight: 500; letter-spacing: 0.5px;
  }
  /* Contact side */
  .card--contact {
    top: 578px;
    background: var(--slate);
    color: var(--white);
  }
  .artwork {
    position: absolute; left: 36px; top: 26px;
    width: 290px; height: 408px;
  }
  .brand {
    position: absolute; left: 365px; top: 60px;
    font-size: 92px; font-weight: 700;
    letter-spacing: 1px; line-height: 1;
    color: var(--white);
  }
  .person { position: absolute; left: 365px; top: 232px; }
  .person__name {
    font-size: 31px; font-weight: 700; color: var(--leaf); line-height: 1.05;
  }
  .person__title { font-size: 18px; font-weight: 500; color: var(--white); }
  .divider {
    position: absolute; left: 365px; width: 364px;
    border-top: 3px dotted var(--dots);
  }
  .divider--one { top: 290px; }
  .divider--two { top: 356px; }
  .contacts {
    position: absolute; left: 365px; top: 298px;
    list-style: none;
    font-size: 19px; line-height: 1.33;
  }
  .contacts__label { font-weight: 600; color: var(--white); }
  .contacts__value { font-weight: 400; color: var(--leaf); }
  .address {
    position: absolute; left: 365px; top: 364px;
    font-style: normal;
    font-size: 19px; line-height: 1.35;
    color: var(--leaf);
  }
</style>
</head>
<body>
<main class="sheet">
  <section class="card card--tagline" aria-label="Tagline side">
    <h1 class="tagline">
      <span class="tagline__lead">glow</span>
      <span class="tagline__rest">From the</span>
      <span class="tagline__rest">Roots Up</span>
    </h1>
    <p class="website">www.plurecare.com</p>
  </section>

  <section class="card card--contact" aria-label="Contact side">
    <svg class="artwork" role="img" aria-label="Illustration of green leaves growing from a DNA helix" viewBox="0 0 290 408" preserveAspectRatio="none">
      <defs>
        <linearGradient id="leafFill" x1="0" y1="0" x2="0" y2="1">
          <stop offset="0" stop-color="#8dc63f"/>
          <stop offset="0.55" stop-color="#1f9a4a"/>
          <stop offset="0.78" stop-color="#7dbb42"/>
          <stop offset="1" stop-color="#d6d6d6"/>
        </linearGradient>
      </defs>
      <rect x="0" y="0" width="290" height="408" rx="40" fill="url(#leafFill)"/>
    </svg>

    <p class="brand">Plure</p>

    <div class="person">
      <p class="person__name">Dana Morel</p>
      <p class="person__title">CEO</p>
    </div>

    <div class="divider divider--one"></div>
    <ul class="contacts">
      <li><span class="contacts__label">Phone:</span> <span class="contacts__value">(555).010.2030</span></li>
      <li><span class="contacts__label">Email:</span> <span class="contacts__value">hello@plurecare.com</span></li>
    </ul>
    <div class="divider divider--two"></div>

    <address class="address">
      Your Address, 2nd Ste<br>
      Fernvale, Ohio 4321, USA
    </address>
  </section>
</main>
</body>
</html>
```